Veltrano.co - Polar Expeditions Specialists

We need a modern, visually striking business card for Veltrano.co, a company specialized in selling expedition cruises to the most remote regions on Earth, with a focus on the Arctic and Antarctica. The design should instantly communicate that the cardholder is an expert in polar travel. Use clean, premium aesthetics with cool tones like icy blue and white, possibly incorporating polar imagery (ice, glaciers, penguins, etc.)

Attached the logo

Contact Information for Business Card

Feels high-end and trustworthy.. Visually memorable — encourages people to keep it

Colors
0054AA
0677BA
7BADD7
CADEEF
E8F1F8

Requirements
Must have
• ice, glaciers, penguins, montains
Nice to have
• modern, transparente,

```html
<!DOCTYPE html>
<html lang="en">
<head>
<meta charset="utf-8">
<title>Veltrano.co – Business Card</title>
<link rel="stylesheet" href="https://fonts.googleapis.com/css2?family=Poppins:wght@600;700;800&family=Lato:wght@400;700&display=swap">
<style>
  :root {
    --backdrop: #2e2e30;
    --brand-blue: #3677b8;
    --deep-blue: #0054aa;
    --ice-blue: #7badd7;
    --card-white: #ffffff;
    --ink: #1c1c1c;
  }
  * { box-sizing: border-box; margin: 0; padding: 0; }
  html, body {
    width: 1200px;
    height: 694px;
    overflow: hidden;
    background: var(--backdrop);
  }
  .canvas {
    position: relative;
    width: 1200px;
    height: 694px;
    display: flex;
    align-items: center;
    justify-content: center;
    gap: 40px;
  }
  .card {
    position: relative;
    width: 540px;
    height: 310px;
    border-radius: 24px;
    overflow: hidden;
    box-shadow: 0 18px 40px rgba(0, 0, 0, 0.45);
  }

  /* Front face */
  .card-front {
    background: var(--brand-blue);
    display: flex;
    flex-direction: column;
    align-items: center;
    justify-content: center;
    color: var(--card-white);
  }
  .brand-name {
    font-family: "Poppins", sans-serif;
    font-weight: 800;
    font-size: 60px;
    line-height: 1;
    letter-spacing: 0.5px;
  }
  .brand-tagline {
    font-family: "Poppins", sans-serif;
    font-weight: 600;
    font-size: 17px;
    margin-top: 8px;
    letter-spacing: 0.3px;
  }

  /* Back face */
  .card-back {
    background: var(--card-white);
    color: var(--brand-blue);
  }
  .back-content {
    position: absolute;
    left: 36px;
    top: 34px;
    width: 320px;
  }
  .card-back .brand-name {
    font-size: 46px;
    color: var(--brand-blue);
  }
  .card-back .brand-tagline {
    font-size: 14px;
    margin-top: 4px;
    color: var(--brand-blue);
  }
  .holder-name {
    font-family: "Poppins", sans-serif;
    font-weight: 700;
    font-size: 22px;
    margin-top: 22px;
    line-height: 1.1;
  }
  .holder-role {
    font-family: "Lato", sans-serif;
    font-size: 14px;
    color: var(--ink);
    margin-top: 4px;
  }
  .contact-list {
    list-style: none;
    margin-top: 12px;
    font-family: "Lato", sans-serif;
    font-size: 13.5px;
    color: var(--ink);
  }
  .contact-item {
    display: flex;
    align-items: center;
    gap: 8px;
    line-height: 1.55;
  }
  .contact-icon {
    width: 14px;
    height: 14px;
    flex: none;
    fill: var(--brand-blue);
  }
  .address {
    font-family: "Lato", sans-serif;
    font-size: 13.5px;
    color: var(--ink);
    margin-top: 8px;
    line-height: 1.45;
  }
  .polar-illustration {
    position: absolute;
    right: 0;
    top: 40px;
    width: 170px;
    height: 270px;
    border-top-left-radius: 90px;
    background: linear-gradient(180deg, var(--brand-blue) 0%, #2f6fb0 100%);
  }
</style>
</head>
<body>
  <main class="canvas">
    <section class="card card-front" aria-label="Card front">
      <p class="brand-name">Veltrano.co</p>
      <p class="brand-tagline">Polar Expeditions Specialists</p>
    </section>

    <section class="card card-back" aria-label="Card back">
      <div class="back-content">
        <p class="brand-name">Veltrano.co</p>
        <p class="brand-tagline">Polar Expeditions Specialists</p>
        <p class="holder-name">Marcus Hale</p>
        <p class="holder-role">Owner</p>
        <ul class="contact-list">
          <li class="contact-item">
            <svg class="contact-icon" viewBox="0 0 24 24" aria-hidden="true"><path d="M6.6 10.8a15.1 15.1 0 0 0 6.6 6.6l2.2-2.2a1 1 0 0 1 1-.25 11.4 11.4 0 0 0 3.6.57 1 1 0 0 1 1 1V20a1 1 0 0 1-1 1A17 17 0 0 1 3 4a1 1 0 0 1 1-1h3.5a1 1 0 0 1 1 1c0 1.25.2 2.45.57 3.6a1 1 0 0 1-.25 1z"/></svg>
            <span>055-210 384 617</span>
          </li>
          <li class="contact-item">
            <svg class="contact-icon" viewBox="0 0 24 24" aria-hidden="true"><path d="M2 5h20v14H2z M3.5 6.5 12 13l8.5-6.5" /></svg>
            <span>hello@veltrano.co</span>
          </li>
          <li class="contact-item">
            <svg class="contact-icon" viewBox="0 0 24 24" aria-hidden="true"><circle cx="12" cy="12" r="10"/><path d="M2 12h20M12 2c3 3 3 17 0 20M12 2c-3 3-3 17 0 20" stroke="#fff" stroke-width="1.5" fill="none"/></svg>
            <span>www.veltrano.co</span>
          </li>
        </ul>
        <p class="address">18, Harbour Lane, Northport<br>60214, Norway</p>
      </div>
      <div class="polar-illustration" role="img" aria-label="Large polar bear silhouette with penguins in brand blue"></div>
    </section>
  </main>
</body>
</html>
```